Business Card Design

My business is writing crime novels to entertain readers. I write legal thrillers and mysteries. I need a card for publishers, agents, other authors, and media.

Industry/Entity Type

Legal

Contact Information for Business Card

Paul Derrow
www.derrowfiction.example
pauljderrow@inkpost.example
0064 27 5190472

```html
<!DOCTYPE html>
<html lang="en">
<head>
<meta charset="utf-8">
<title>Paul Derrow – Business Card</title>
<link rel="stylesheet" href="https://fonts.googleapis.com/css2?family=Gochi+Hand&family=Jost:wght@400&display=swap">
<style>
  :root {
    --stage: #e8e3d9;
    --card-black: #050505;
    --ink-red: #e0161b;
    --swirl-red-deep: #3a0606;
    --swirl-red-soft: #1a0303;
    --text-white: #f4f4f4;
    --portrait-dark: #1b1b1b;
    --portrait-mid: #4a4a4a;
    --portrait-light: #d9d5d0;
  }
  * { margin: 0; padding: 0; box-sizing: border-box; }
  html, body {
    width: 1200px;
    height: 729px;
    overflow: hidden;
    background: var(--stage);
  }
  .canvas {
    position: relative;
    width: 1200px;
    height: 729px;
  }
  .business-card {
    position: absolute;
    left: 110px;
    top: 107px;
    width: 980px;
    height: 515px;
    border-radius: 36px;
    background: var(--card-black);
    overflow: hidden;
    box-shadow: 0 10px 30px rgba(0,0,0,0.35);
  }
  .ornament-area {
    position: absolute;
    left: 0;
    top: 0;
    width: 380px;
    height: 400px;
    background: radial-gradient(ellipse at 40% 40%, var(--swirl-red-deep) 0%, var(--swirl-red-soft) 45%, rgba(5,5,5,0) 75%);
  }
  .portrait-area {
    position: absolute;
    right: 28px;
    top: 48px;
    width: 380px;
    height: 467px;
    background:
      radial-gradient(ellipse at 38% 22%, var(--portrait-mid) 0%, rgba(74,74,74,0) 30%),
      radial-gradient(ellipse at 45% 78%, var(--portrait-light) 0%, rgba(217,213,208,0) 22%),
      linear-gradient(180deg, var(--card-black) 0%, var(--portrait-dark) 40%, var(--portrait-dark) 100%);
  }
  .author-name {
    position: absolute;
    left: 120px;
    top: 290px;
    font-family: "Gochi Hand", cursive;
    font-size: 54px;
    font-weight: 400;
    color: var(--ink-red);
    letter-spacing: 1px;
  }
  .contact-list {
    position: absolute;
    left: 140px;
    top: 370px;
    list-style: none;
  }
  .contact-item {
    display: flex;
    align-items: center;
    height: 40px;
    font-family: "Jost", sans-serif;
    font-size: 25px;
    color: var(--text-white);
  }
  .contact-icon {
    width: 22px;
    height: 22px;
    margin-right: 18px;
    flex: none;
  }
</style>
</head>
<body>
<div class="canvas">
  <div class="business-card">
    <div class="ornament-area" role="img" aria-label="Dark red decorative swirl pattern"></div>
    <div class="portrait-area" role="img" aria-label="Portrait photograph of the author in a dark leather jacket and white shirt"></div>

    <h1 class="author-name">Paul Derrow</h1>

    <ul class="contact-list">
      <li class="contact-item">
        <svg class="contact-icon" viewBox="0 0 24 24" aria-hidden="true">
          <path fill="var(--ink-red)" d="M3 9c0-3 4-5 9-5s9 2 9 5v2h-5V9H8v2H3z"/>
          <path fill="var(--ink-red)" d="M6 12h12l2 8H4z"/>
          <circle cx="12" cy="16" r="2" fill="var(--card-black)"/>
        </svg>
        <span>0064 27 5190472</span>
      </li>
      <li class="contact-item">
        <svg class="contact-icon" viewBox="0 0 24 24" aria-hidden="true">
          <rect x="2" y="5" width="20" height="14" rx="1" fill="var(--ink-red)"/>
          <path d="M2.5 6l9.5 7 9.5-7" fill="none" stroke="var(--card-black)" stroke-width="1.6"/>
        </svg>
        <span>pauljderrow@inkpost.example</span>
      </li>
      <li class="contact-item">
        <svg class="contact-icon" viewBox="0 0 24 24" aria-hidden="true">
          <circle cx="12" cy="12" r="10" fill="var(--ink-red)"/>
          <g fill="none" stroke="var(--card-black)" stroke-width="1.3">
            <ellipse cx="12" cy="12" rx="4.5" ry="10"/>
            <path d="M2 12h20M4 7h16M4 17h16"/>
          </g>
        </svg>
        <span>www.derrowfiction.example</span>
      </li>
    </ul>
  </div>
</div>
</body>
</html>
```